Fresh, modern, fun business card for pediatric dental practice

Need a business card for fresh, modern, fun pediatric dental practice

Clean look that matches our website's font and colors

We prefer the look of curved corners on business cards

Target Market(s)

parents (mothers) of young children, professionals, mid-high class

Industry/Entity Type

Dental

Contact Information for Business Card

Maplebrook Pediatric Dentistry
482 Quarry Lane
Suite 517
Cedarton, PA 17500
717.555.0193
www.maplebrookkidsdental.example

Mei-Ran Tsai, DMD
Corinne Walbeck, DMD
(we are working on our email address, but we would like that on the card as well)

Font styles to use
Sans Serif

Requirements
Must have
• All info; we would also like to make cards for individual staff members
• colors from our website and color palatte, attatched
• use same font and design as website for branding
Nice to have
• clean, simple card that has a pop of color
• we would like to see a few designs with our tag line "where smiles get brighter"
• we are not sure if we want to have it on there or not
• we would like to see a few designs incorporating the ribbon graphic on our website where the word WELCOME is

```html
<!DOCTYPE html>
<html lang="en">
<head>
<meta charset="utf-8">
<title>Maplebrook Pediatric Dentistry — Business Cards</title>
<link rel="stylesheet" href="https://fonts.googleapis.com/css2?family=Open+Sans:wght@600&family=Roboto:wght@400&family=Roboto+Condensed:wght@500&display=swap">
<style>
  :root {
    --backdrop: #2a2a2a;
    --paper: #f7f7f5;
    --magenta: #d02c91;
    --sun: #fbb423;
    --ink-grey: #555555;
    --white: #ffffff;
  }
  * { margin: 0; padding: 0; box-sizing: border-box; }
  html, body { width: 1200px; height: 960px; overflow: hidden; }
  body { background: var(--backdrop); position: relative; }

  .card {
    position: absolute;
    border-radius: 18px;
    overflow: hidden;
  }

  /* Front */
  .card-front {
    left: 320px; top: 100px; width: 610px; height: 350px;
    background: var(--paper);
  }
  .front-mark {
    position: absolute; left: 0; right: 0; top: 120px;
    display: flex; flex-direction: column; align-items: center; gap: 22px;
  }
  .front-mark .dot {
    width: 44px; height: 44px; border-radius: 50%;
    background: var(--sun);
  }
  .brand-name {
    font-family: "Open Sans", sans-serif;
    font-weight: 600;
    color: var(--sun);
    letter-spacing: 2px;
    line-height: 1;
    white-space: nowrap;
  }
  .front-mark .brand-name { font-size: 46px; }
  .front-url {
    position: absolute; left: 0; right: 0; top: 302px;
    text-align: center;
    font-family: "Roboto", sans-serif;
    font-size: 14px;
    letter-spacing: 3.2px;
    color: var(--ink-grey);
    white-space: nowrap;
  }

  /* Back */
  .card-back {
    left: 320px; top: 493px; width: 600px; height: 342px;
    background: var(--magenta);
  }
  .card-back .brand-name {
    position: absolute; left: 40px; top: 76px;
    font-size: 42px;
  }
  .doctors {
    position: absolute; left: 40px; top: 201px;
    font-family: "Roboto Condensed", sans-serif;
    font-weight: 500;
    font-size: 21px;
    line-height: 24px;
    color: var(--sun);
    text-transform: uppercase;
    white-space: nowrap;
  }
  .address {
    position: absolute; left: 40px; top: 256px;
    font-family: "Roboto", sans-serif;
    font-size: 14.5px;
    line-height: 19px;
    color: var(--white);
    font-style: normal;
    white-space: nowrap;
  }
  .contact {
    position: absolute; right: 42px; top: 272px;
    font-family: "Roboto", sans-serif;
    font-size: 14.5px;
    line-height: 20px;
    color: var(--white);
    list-style: none;
    text-align: right;
    white-space: nowrap;
  }
  .contact li { display: flex; align-items: center; justify-content: flex-end; gap: 8px; }
  .contact svg { width: 13px; height: 13px; flex: none; }
</style>
</head>
<body>

  <section class="card card-front" aria-label="Business card front">
    <div class="front-mark">
      <span class="dot" aria-hidden="true"></span>
      <span class="brand-name">maplebrook</span>
    </div>
    <p class="front-url">www.maplebrookkidsdental.example</p>
  </section>

  <section class="card card-back" aria-label="Business card back">
    <span class="brand-name">maplebrook</span>
    <p class="doctors">Mei-Ran Tsai, DMD<br>Corinne Walbeck, DMD</p>
    <address class="address">
      Maplebrook Pediatric Dentistry<br>
      482 Quarry Lane<br>
      Suite 517, Cedarton, PA 17500
    </address>
    <ul class="contact">
      <li>717.555.0193
        <svg viewBox="0 0 24 24" aria-hidden="true"><path fill="#fbb423" d="M6.6 10.8a15.1 15.1 0 0 0 6.6 6.6l2.2-2.2c.3-.3.7-.4 1-.2 1.1.4 2.3.6 3.6.6.6 0 1 .4 1 1V20c0 .6-.4 1-1 1A17 17 0 0 1 3 4c0-.6.4-1 1-1h3.5c.6 0 1 .4 1 1 0 1.3.2 2.5.6 3.6.1.3 0 .7-.2 1z"/></svg>
      </li>
      <li>maplebrookkidsdental.example
        <svg viewBox="0 0 24 24" aria-hidden="true"><circle cx="12" cy="12" r="11" fill="#fbb423"/><path d="M3 12h18M12 1c3 3 4 7 4 11s-1 8-4 11M12 1c-3 3-4 7-4 11s1 8 4 11" stroke="#d02c91" stroke-width="1.6" fill="none"/></svg>
      </li>
    </ul>
  </section>

</body>
</html>
```